Oil and Gas Exploration and Production company needs a business card design

We need a business card design using our logo and colors in the logo. We want a mainstream design.

```html
<!DOCTYPE html>
<html lang="en">
<head>
<meta charset="utf-8">
<title>Sorel Oil &amp; Gas – Business Card</title>
<link href="https://fonts.googleapis.com/css2?family=Crimson+Pro:wght@400;600;700&display=swap" rel="stylesheet">
<style>
  :root {
    --page-bg: #e6e6e6;
    --card-light: #f3f3f3;
    --card-dark: #070707;
    --ink: #0b0b0b;
    --gold: #c9962b;
    --white: #ffffff;
    --divider: #8a8a8a;
  }
  * { margin: 0; padding: 0; box-sizing: border-box; }
  html, body {
    width: 1200px; height: 586px; overflow: hidden;
    background: var(--page-bg);
    font-family: "Crimson Pro", Georgia, serif;
  }
  .card {
    position: absolute; left: 150px; top: 23px;
    width: 900px; height: 540px;
    background: var(--card-light);
    overflow: hidden;
  }
  .brand {
    position: absolute; left: 0; right: 0; top: 0; height: 313px;
    display: flex; align-items: center; justify-content: center; gap: 22px;
  }
  .brand-dot {
    width: 56px; height: 56px; border-radius: 50%;
    background: var(--gold);
  }
  .brand-name {
    font-weight: 700; font-size: 78px; line-height: 1;
    color: var(--ink); letter-spacing: 0.5px;
  }
  .rule { position: absolute; left: 0; right: 0; background: var(--card-dark); }
  .rule--one { top: 313px; height: 4px; }
  .rule--two { top: 321px; height: 4px; }
  .contact-band {
    position: absolute; left: 0; right: 0; top: 330px; bottom: 0;
    background: var(--card-dark);
    color: var(--white);
  }
  .person {
    position: absolute; right: 494px; top: 52px; text-align: right;
  }
  .person-name { color: var(--gold); font-weight: 600; font-size: 21px; line-height: 1; }
  .person-title { font-size: 17px; margin-top: 6px; line-height: 1; }
  .person-address { font-weight: 700; font-size: 19px; margin-top: 28px; line-height: 1; }
  .divider {
    position: absolute; left: 451px; top: 42px; width: 2px; height: 115px;
    background: linear-gradient(to bottom, transparent, var(--divider) 50%, transparent);
  }
  .contact-list {
    position: absolute; left: 490px; top: 52px; list-style: none;
  }
  .contact-item {
    display: flex; align-items: center; gap: 12px;
    font-size: 19px; line-height: 1; height: 22px; margin-bottom: 14px;
  }
  .contact-icon { width: 17px; height: 14px; fill: var(--gold); flex: none; }
</style>
</head>
<body>
  <div class="card">
    <div class="brand">
      <span class="brand-dot"></span>
      <span class="brand-name">Sorel Oil &amp; Gas</span>
    </div>
    <div class="rule rule--one"></div>
    <div class="rule rule--two"></div>
    <div class="contact-band">
      <div class="person">
        <p class="person-name">Maren Holt</p>
        <p class="person-title">Chief Executive Offer</p>
        <p class="person-address">410 Ridgeline Ave, Suite 210, NC 27000</p>
      </div>
      <div class="divider"></div>
      <ul class="contact-list">
        <li class="contact-item">
          <svg class="contact-icon" viewBox="0 0 17 14" aria-hidden="true">
            <path d="M1 5 Q8.5 0 16 5 L14 7 L11.5 5.5 L11.5 4 Q8.5 3 5.5 4 L5.5 5.5 L3 7 Z"/>
            <path d="M4 7 L13 7 L15 13 L2 13 Z"/>
          </svg>
          <span>555.014.2280</span>
        </li>
        <li class="contact-item">
          <svg class="contact-icon" viewBox="0 0 17 14" aria-hidden="true">
            <rect x="4" y="0" width="9" height="4"/>
            <rect x="0" y="5" width="17" height="6" rx="1"/>
            <rect x="4" y="9" width="9" height="5"/>
          </svg>
          <span>555.014.2291</span>
        </li>
        <li class="contact-item">
          <svg class="contact-icon" viewBox="0 0 17 14" aria-hidden="true">
            <path d="M0 2 L17 2 L17 13 L0 13 Z M1 3 L8.5 9 L16 3 Z" fill-rule="evenodd"/>
          </svg>
          <span>mholt@sorelenergy.com</span>
        </li>
      </ul>
    </div>
  </div>
</body>
</html>
```